I would like a single page website for Skyward Rentals Pacific. In the file list provided there is basic information to be included as well as our logo with colors, fonts and images to be included.
Site must be very simple and be able to be loaded onto smart phones etc very quickly.
Site needs to be very smart in appearance

Target Market(s)

All prospective drone customers from Police to Parties.

Industry/Entity Type

Hire

Requirements
Must have
• Must have variation of color schemes supplied
Nice to have
• Must be very eye catching without going over the top
Should not have
• Anything slow to load.

```html
<!DOCTYPE html>
<html lang="en">
<head>
<meta charset="utf-8">
<title>Skyward Rentals Pacific</title>
<link href="https://fonts.googleapis.com/css2?family=Open+Sans:wght@300;400;600&display=swap" rel="stylesheet">
<style>
:root{
  --green:#bfd641;
  --text:#555;
  --text-dark:#333;
  --white:#fff;
  --grey-btn:#6d6d6d;
  --footer-bg:#f7f7f7;
  --rule:#e3e3e3;
  --icon:#6d6d6d;
}
*{margin:0;padding:0;box-sizing:border-box}
html,body{width:1200px;height:2400px;overflow:hidden;background:var(--white)}
body{font-family:"Open Sans",Arial,sans-serif;color:var(--text);position:relative}
.abs{position:absolute}

/* header */
.site-header{position:absolute;left:0;top:0;width:1200px;height:100px}
.brand{position:absolute;left:93px;top:40px;display:flex;align-items:center;gap:10px}
.brand-dot{width:18px;height:18px;border-radius:50%;background:var(--green)}
.brand-name{font-size:26px;font-weight:600;color:var(--green);letter-spacing:.5px}
.phone{position:absolute;right:93px;top:32px;font-size:17px;color:var(--text);display:flex;align-items:center;gap:7px;font-weight:300}
.main-nav{position:absolute;left:452px;top:64px;display:flex}
.main-nav a{font-size:13px;color:var(--text-dark);text-decoration:none;text-transform:uppercase;padding:0 20px;height:36px;line-height:22px;position:relative}
.main-nav a.active{color:var(--green)}
.main-nav a.active::after{content:"";position:absolute;left:0;right:0;bottom:0;height:3px;background:var(--green)}
.search{position:absolute;left:922px;top:64px;width:186px;height:24px;border:1px solid #d5d5d5;font-size:10px;color:#aaa;padding:5px 8px}
.search svg{position:absolute;right:7px;top:5px}

/* hero */
.hero{position:absolute;left:0;top:100px;width:1200px;height:569px}
.hero-photo{position:absolute;inset:0;background:radial-gradient(ellipse at 62% 40%,#9a9a9a 0%,#6e6e6e 35%,#3a3a3a 70%,#7a7a7a 100%)}
.hero-circle{position:absolute;left:184px;top:122px;width:362px;height:362px;border-radius:50%;background:rgba(80,80,82,.88);text-align:center;padding-top:92px}
.hero-title-top{font-size:38px;color:var(--green);font-weight:400;line-height:1.1}
.hero-title-bottom{font-size:60px;color:#2a2a2a;font-weight:300;line-height:1.05}
.hero-text{font-size:14px;color:#e6e6e6;width:300px;margin:12px auto 0;line-height:1.35}
.btn-green{display:inline-block;margin-top:26px;background:var(--green);color:var(--white);font-size:14px;font-weight:600;padding:8px 21px}
.slider-dots{position:absolute;left:571px;top:531px;display:flex;gap:10px}
.slider-dots span{width:7px;height:7px;border-radius:50%;background:var(--white)}
.slider-dots span.on{background:var(--green)}

/* welcome */
.welcome{position:absolute;left:0;top:669px;width:1200px;height:222px;text-align:center}
.section-title{font-size:27px;font-weight:400;text-transform:uppercase}
.welcome .section-title{color:var(--green);margin-top:68px}
.welcome p{width:1040px;margin:14px auto 0;font-size:14.5px;line-height:24px;color:var(--text-dark)}

/* services */
.services{position:absolute;left:0;top:891px;width:1200px;height:922px;background:var(--green)}
.services .section-title{color:var(--white);text-align:center;margin-top:54px}
.service{position:absolute;width:300px;text-align:center;color:var(--white)}
.service-icon{width:100px;height:100px;border-radius:50%;background:var(--white);margin:0 auto;display:flex;align-items:center;justify-content:center}
.service h3{font-size:16.5px;font-weight:600;line-height:22px;margin-top:28px;height:44px}
.service p{font-size:12.5px;font-weight:300;line-height:21px;margin-top:22px}
.btn-grey{position:absolute;left:510px;top:810px;width:180px;height:43px;background:var(--grey-btn);color:var(--white);font-size:16px;font-weight:600;text-align:center;line-height:43px}

/* feature */
.feature{position:absolute;left:0;top:1813px;width:1200px;height:331px}
.feature-photo{position:absolute;left:192px;top:56px;width:344px;height:206px;border-radius:8px;background:radial-gradient(ellipse at center,#e2e2e2 0%,#f4f4f4 60%,#fff 100%)}
.feature-title{position:absolute;left:565px;top:96px;font-size:27px;color:var(--green);font-weight:400;text-transform:uppercase}
.feature-sub{position:absolute;left:567px;top:138px;font-size:16px;color:var(--text-dark);font-weight:600;text-transform:uppercase}
.feature-text{position:absolute;left:567px;top:174px;width:400px;font-size:12.5px;line-height:21px;font-weight:300;color:var(--text)}

/* footer */
.site-footer{position:absolute;left:0;top:2144px;width:1200px;height:195px;background:var(--footer-bg)}
.footer-col{position:absolute;top:26px;list-style:none;font-size:13px;line-height:21.6px;color:var(--text)}
.social{position:absolute;left:958px;top:26px}
.social li{list-style:none;display:flex;align-items:center;justify-content:space-between;width:150px;height:21.6px;margin-bottom:21.6px;font-size:13px}
.social-dot{width:22px;height:22px;border-radius:50%;border:1.5px solid #2b7ab8}
.bottom-bar{position:absolute;left:0;top:2339px;width:1200px;height:61px;border-top:1px solid var(--rule);text-align:center;font-size:13px;line-height:52px;color:var(--text)}
</style>
</head>
<body>

<header class="site-header">
  <div class="brand"><span class="brand-dot"></span><span class="brand-name">Skyward Rentals Pacific</span></div>
  <div class="phone">
    <svg width="14" height="14" viewBox="0 0 24 24"><path fill="#bfd641" d="M6.6 10.8a15.1 15.1 0 0 0 6.6 6.6l2.2-2.2c.3-.3.7-.4 1-.2 1.1.4 2.3.6 3.6.6.6 0 1 .4 1 1V20c0 .6-.4 1-1 1A17 17 0 0 1 3 4c0-.6.4-1 1-1h3.5c.6 0 1 .4 1 1 0 1.3.2 2.5.6 3.6.1.3 0 .7-.2 1z"/></svg>
    0400 555 219
  </div>
  <nav class="main-nav">
    <a class="active">Home</a><a>About Us</a><a>Services</a><a>FAQ's</a><a>Contact Us</a>
  </nav>
  <div class="search">Search
    <svg width="12" height="12" viewBox="0 0 24 24"><circle cx="10" cy="10" r="6.5" fill="none" stroke="#444" stroke-width="3"/><path d="M15 15l6 6" stroke="#444" stroke-width="3.5" stroke-linecap="round"/></svg>
  </div>
</header>

<section class="hero">
  <div class="hero-photo" role="img" aria-label="Black and white photo of a couple, blurred, with a white camera drone hovering in front"></div>
  <div class="hero-circle">
    <div class="hero-title-top">SKYWARD RENTALS</div>
    <div class="hero-title-bottom">PACIFIC</div>
    <p class="hero-text">Lorem Ipsum is simply dummy text of the printing and typesetting industry. Lorem Ipsum has been the industry's standard dummy text ever</p>
    <span class="btn-green">Read More</span>
  </div>
  <div class="slider-dots"><span class="on"></span><span></span><span></span><span></span></div>
</section>

<section class="welcome">
  <h2 class="section-title">Welcome to Skyward Rentals Pacific</h2>
  <p>ASRA certified company and ASRA endorsed pilot, with Full Public Liability Insurance. All operating&nbsp; licences are in place and are carried on the operator. All drones are maintained to full ASRA compliance standards</p>
</section>

<section class="services">
  <h2 class="section-title">Our Main Services</h2>

  <div class="service" style="left:103px;top:153px">
    <div class="service-icon"><svg width="30" height="30" viewBox="0 0 24 24" fill="#6d6d6d"><rect x="3" y="13" width="18" height="8"/><rect x="5" y="9" width="2" height="4"/><rect x="11" y="9" width="2" height="4"/><rect x="17" y="9" width="2" height="4"/><circle cx="6" cy="6.5" r="1.4"/><circle cx="12" cy="6.5" r="1.4"/><circle cx="18" cy="6.5" r="1.4"/></svg></div>
    <h3>Special Occasions, Children's Birthday Parties, Weddings</h3>
    <p>Lorem Ipsum is simply dummy text of the printing and typesetting industry. Lorem Ipsum has been the industry's standard dummy text ever</p>
  </div>
  <div class="service" style="left:450px;top:153px">
    <div class="service-icon"><svg width="30" height="30" viewBox="0 0 24 24" fill="#6d6d6d"><path d="M8 3h3.2v3h1.6V3H16l5 18h-8.2v-4h-1.6v4H3zM11.2 9v4h1.6V9z"/></svg></div>
    <h3>Sporting events –4K&nbsp; Video of yourself participating in marathons etc</h3>
    <p>Lorem Ipsum is simply dummy text of the printing and typesetting industry. Lorem Ipsum has been the industry's standard dummy text ever</p>
  </div>
  <div class="service" style="left:797px;top:153px">
    <div class="service-icon"><svg width="30" height="30" viewBox="0 0 24 24" fill="#6d6d6d"><path d="M12 3l10 9h-3v9h-5v-6h-4v6H5v-9H2z"/></svg></div>
    <h3>Real Estate Brochures</h3>
    <p>Lorem Ipsum is simply dummy text of the printing and typesetting industry. Lorem Ipsum has been the industry's standard dummy text ever</p>
  </div>

  <div class="service" style="left:103px;top:483px">
    <div class="service-icon"><svg width="28" height="30" viewBox="0 0 20 24" fill="#6d6d6d"><path d="M3 1h14v22H3zM6 4v2h3V4zm5 0v2h3V4zM6 9v2h3V9zm5 0v2h3V9zM6 14v2h3v-2zm5 0v2h3v-2zM8 19v4h4v-4z" fill-rule="evenodd"/></svg></div>
    <h3>Construction project updates for remote stake holders</h3>
    <p>Lorem Ipsum is simply dummy text of the printing and typesetting industry. Lorem Ipsum has been the industry's standard dummy text ever</p>
  </div>
  <div class="service" style="left:450px;top:483px">
    <div class="service-icon"><svg width="30" height="30" viewBox="0 0 24 24" fill="#6d6d6d"><path d="M9 4h6v3h6v5H3V7h6zm2 1.5V7h2V5.5zM3 13.5h7v1.5h4v-1.5h7V20H3z"/></svg></div>
    <h3>Surveillance – Police, Local councils worksafe etc</h3>
    <p>Lorem Ipsum is simply dummy text of the printing and typesetting industry. Lorem Ipsum has been the industry's standard dummy text ever</p>
  </div>
  <div class="service" style="left:797px;top:483px">
    <div class="service-icon"><svg width="30" height="30" viewBox="0 0 24 24"><circle cx="10" cy="10" r="6.5" fill="none" stroke="#6d6d6d" stroke-width="3"/><path d="M15 15l6 6" stroke="#6d6d6d" stroke-width="3.5" stroke-linecap="round"/></svg></div>
    <h3>Building/Roof Condition Inspections</h3>
    <p>Lorem Ipsum is simply dummy text of the printing and typesetting industry. Lorem Ipsum has been the industry's standard dummy text ever</p>
  </div>

  <div class="btn-grey">View More Services</div>
</section>

<section class="feature">
  <div class="feature-photo" role="img" aria-label="White quadcopter drone with a gimbal camera, on white"></div>
  <h2 class="feature-title">Skyward Rentals Pacific</h2>
  <div class="feature-sub">4K Video Footage&nbsp; | 12MP Images</div>
  <p class="feature-text">Lorem Ipsum is simply dummy text of the printing and typesetting industry. Lorem Ipsum has been the industry's standard dummy text ever since the 1500s, when an unknown printer took a galley of type and scrambled it to make a type specimen book.</p>
</section>

<footer class="site-footer">
  <ul class="footer-col" style="left:93px"><li>Home</li><li>About Us</li><li>Services</li><li>Faq's</li><li>Contact Us</li></ul>
  <ul class="footer-col" style="left:354px"><li>Privacy Policy</li><li>Terms &amp; Conditions</li></ul>
  <ul class="footer-col" style="left:614px"><li>Skyward Rentals Office</li><li>Harbour Lane 42b</li><li>4000 Brisbane</li><li>Australia</li><li>Telephone: +61 7 5550 1984</li><li>E-mail: hello@skywardrentals.example</li></ul>
  <ul class="social">
    <li>Chatter <span class="social-dot"></span></li>
    <li>Crowdly <span class="social-dot"></span></li>
    <li>Linkup <span class="social-dot"></span></li>
  </ul>
</footer>
<div class="bottom-bar">© 2015 Company Name ,All Rights Reserved</div>

</body>
</html>
```